Business card design needed

I would like a one sided black business card with the information provided above. Refer to my website www.brightvolleyracquets.com.au for an example of colors I have used for my site, would like to keep this consistent for my business cards also, I will upload my logo below.

I am a new small business that provides tennis customers with racquet re stringing, tennis strings and accessories.

Industry/Entity Type

Small Business

Contact Information for Business Card

Bright Volley Tennis

Owen Whitby
Managing Director

brightvolleyracquets@mailbox.example
www.brightvolleyracquets.com.au
0491 726 305

Racquet Restringing/Tennis Strings/Accessories

Requirements
Must have
• Must have my logo and card must be black

```html
<!DOCTYPE html>
<html lang="en">
<head>
<meta charset="utf-8">
<title>Bright Volley Tennis – Business Card</title>
<link rel="stylesheet" href="https://fonts.googleapis.com/css2?family=Source+Sans+3:wght@400;600;700&display=swap">
<style>
  :root {
    --backdrop: #dedbd6;
    --card-black: #040404;
    --volley-green: #b7d433;
    --court-blue: #2b5d9c;
    --text-white: #ffffff;
    --name-grey: #3b3b3b;
  }
  * { box-sizing: border-box; margin: 0; padding: 0; }
  html, body {
    width: 1200px; height: 750px; overflow: hidden;
    background: var(--backdrop);
    font-family: "Source Sans 3", Arial, sans-serif;
  }
  .card {
    position: absolute; left: 75px; top: 75px;
    width: 1050px; height: 598px;
    background: var(--card-black);
    border-radius: 42px;
    overflow: hidden;
    color: var(--text-white);
  }
  .brand {
    position: absolute; left: 0; right: 0; top: 140px;
    display: flex; justify-content: center; align-items: center; gap: 18px;
  }
  .brand-dot {
    width: 34px; height: 34px; border-radius: 50%;
    background: var(--volley-green);
  }
  .brand-name {
    font-size: 56px; font-weight: 700; letter-spacing: 1px;
    color: var(--volley-green); line-height: 1;
  }
  .contact-list {
    position: absolute; left: 110px; top: 333px;
    list-style: none;
  }
  .contact-item {
    display: flex; align-items: center; gap: 10px;
    height: 44px; font-size: 23px;
  }
  .contact-icon { width: 22px; height: 22px; flex: none; }
  .services {
    position: absolute; left: 565px; top: 323px;
    list-style: none;
  }
  .service {
    display: flex; align-items: center; gap: 12px;
    height: 45px; font-size: 32px;
  }
  .service::before {
    content: ""; width: 9px; height: 9px; background: var(--text-white);
  }
  .swoosh { position: absolute; left: 0; top: 0; width: 1050px; height: 598px; }
  .signature {
    position: absolute; left: 482px; top: 541px;
    color: var(--name-grey); font-size: 24px;
  }
  .signature-name { font-size: 31px; font-weight: 700; }
</style>
</head>
<body>
  <main class="card">
    <svg class="swoosh" viewBox="0 0 1050 598" aria-hidden="true">
      <path d="M0,552 Q280,524 548,508 Q300,536 0,596 Z" fill="var(--court-blue)"/>
      <path d="M20,598 Q360,540 750,510 Q955,504 1050,538 L1050,598 Z" fill="var(--volley-green)"/>
    </svg>

    <div class="brand">
      <span class="brand-dot"></span>
      <span class="brand-name">Bright Volley Tennis</span>
    </div>

    <ul class="contact-list">
      <li class="contact-item">
        <svg class="contact-icon" viewBox="0 0 24 24" aria-hidden="true">
          <path d="M2,9 Q12,2 22,9 L20,12 L16,10 L16,8 Q12,6 8,8 L8,10 L4,12 Z M6,12 L18,12 L20,20 L4,20 Z" fill="var(--volley-green)"/>
        </svg>
        <span>0491 726 305</span>
      </li>
      <li class="contact-item">
        <svg class="contact-icon" viewBox="0 0 24 24" aria-hidden="true">
          <rect x="2" y="6" width="20" height="13" fill="none" stroke="var(--volley-green)" stroke-width="2"/>
          <path d="M2,6 L12,14 L22,6" fill="none" stroke="var(--volley-green)" stroke-width="2"/>
        </svg>
        <span>brightvolleyracquets@mailbox.example</span>
      </li>
      <li class="contact-item">
        <svg class="contact-icon" viewBox="0 0 24 24" aria-hidden="true">
          <circle cx="12" cy="12" r="9" fill="var(--volley-green)"/>
          <path d="M3,12 H21 M12,3 V21 M6,6 Q12,10 18,6 M6,18 Q12,14 18,18" stroke="var(--card-black)" stroke-width="1.2" fill="none"/>
        </svg>
        <span>www.brightvolleyracquets.com.au</span>
      </li>
    </ul>

    <ul class="services">
      <li class="service">Racquet Restringing</li>
      <li class="service">Tennis Strings</li>
      <li class="service">Accessories</li>
    </ul>

    <p class="signature"><span class="signature-name">Owen Whitby,</span> Managing Director</p>
  </main>
</body>
</html>
```